life insurance quote website design for lepontdoriole.ca

the web site lepontdoriole.ca need a design. we dont like the actuel one but we are open at all new suggestion. visit us at lepontdoriole.ca and you will understand. the principal concurant is tarifsgarantisnord.ca, calculeo.ca, coutprotecfam.ca. We are a life insurance quote site. we found best price available in the canadien industrie. We absolutly want a design with our form in the front page on the top right side like our concurance, we use wordpress at this time. we want to be able to switch language. and to have a logic form. we want to be able to change the color for each type of insurance quote page.we also need a blog in it to post news. and the site will be SEO accurate.

Target Market(s)

Get client fill the quote form

Industry/Entity Type

Insurance

Number of Pages Required

3 page

Font styles to use
Sans Serif

Requirements
Must have
• logic form on the top right first page
• page template for product info stuff, contact, and who we are, blog
• French site
• custum color
Nice to have
• Wordpress design will be appréciate
• switch language english/french

```html
<!DOCTYPE html>
<html lang="fr">
<head>
<meta charset="utf-8">
<title>lepontdoriole.ca — Soumission d'assurance</title>
<link rel="stylesheet" href="https://fonts.googleapis.com/css2?family=Open+Sans:wght@400;600;700&family=Roboto+Condensed:wght@400;700&display=swap">
<style>
:root{
  --red:#d7262e;
  --red-dark:#a8161d;
  --blue:#1f8fd1;
  --blue-box:#2fa3d6;
  --orange:#f0a32b;
  --green:#5cb85c;
  --pink:#e94e77;
  --navy:#17243f;
  --navy-dark:#0f1a30;
  --text:#555;
  --muted:#999;
  --line:#e3e3e3;
  --bg:#f4f4f4;
}
*{box-sizing:border-box;margin:0;padding:0}
html,body{width:1200px;height:2640px;overflow:hidden}
body{font-family:"Open Sans",Arial,sans-serif;color:var(--text);font-size:13px;line-height:1.6;background:#fff}
.wrap{width:1000px;margin:0 auto;position:relative}
h1,h2,h3,h4{font-family:"Roboto Condensed","Arial Narrow",sans-serif;font-weight:700;text-transform:uppercase}

/* header */
.site-header{height:120px;background:#fff;border-bottom:1px solid var(--line)}
.site-header .wrap{height:120px}
.brand{position:absolute;left:20px;top:22px;display:flex;align-items:center;gap:12px}
.brand-dot{width:62px;height:62px;border-radius:50%;background:var(--red)}
.brand-name{font-weight:700;font-size:26px;color:var(--red);font-family:"Open Sans",sans-serif}
.topbar{position:absolute;right:-60px;top:14px;display:flex;gap:26px;font-size:12px;color:#666;align-items:center}
.topbar span{display:flex;align-items:center;gap:6px}
.topbar svg{width:14px;height:14px}
.main-nav{position:absolute;right:-40px;top:66px;display:flex;gap:34px;font-size:13px;font-weight:600;color:#444}
.main-nav a{color:inherit;text-decoration:none;padding-bottom:8px}
.main-nav a.active{color:var(--red);border-bottom:3px solid var(--red)}

/* hero */
.hero{height:440px;position:relative;background:linear-gradient(160deg,#7fb7d8 0%,#b9d6a0 45%,#6f9b3f 75%,#4f7a2c 100%)}
.hero-photo{position:absolute;inset:0}
.hero-brand{position:absolute;left:130px;top:150px;display:flex;align-items:center;gap:16px}
.hero-brand .sq{width:70px;height:70px;background:var(--red)}
.hero-brand .name{font-size:44px;font-weight:700;color:#fff;font-family:"Open Sans",sans-serif}
.quote-form{position:absolute;right:40px;top:46px;width:380px;height:336px;background:var(--red);color:#fff;padding:0 16px 14px}
.quote-form h2{background:var(--red-dark);margin:0 -16px 12px;padding:10px;text-align:center;font-size:17px;letter-spacing:.5px}
.qf-row{display:flex;align-items:center;gap:10px;margin-bottom:8px;font-size:12px}
.qf-row label{width:110px;text-align:right}
.qf-select{flex:1;height:22px;background:#fff;border-radius:2px;position:relative}
.qf-select::after{content:"";position:absolute;right:8px;top:8px;border:5px solid transparent;border-top-color:#777}
.qf-radios{justify-content:center;gap:22px;font-weight:600}
.qf-radios i{display:inline-block;width:10px;height:10px;border-radius:50%;background:#fff;margin-right:5px;vertical-align:-1px}
.qf-grid{display:grid;grid-template-columns:1fr 1fr;gap:7px 10px;margin:4px 0 10px}
.qf-field{height:24px;background:#fff;border-radius:2px;color:#999;font-size:11px;padding:3px 7px}
.qf-foot{display:flex;align-items:center;gap:10px}
.captcha{width:110px;height:34px;background:#eee;color:#555;font-family:"Roboto Condensed",sans-serif;font-size:20px;font-style:italic;text-align:center;line-height:34px;letter-spacing:3px}
.qf-foot .qf-field{flex:1;height:30px}
.btn-send{background:#fff;color:var(--red);font-weight:700;padding:6px 16px;font-size:12px}

/* product boxes */
.products{height:260px;padding-top:20px;background:var(--bg)}
.products .wrap{display:flex;gap:20px}
.product{flex:1;height:200px;color:#fff;text-align:center;display:flex;flex-direction:column}
.product h3{font-size:18px;padding:22px 10px 8px}
.product p{font-size:11.5px;padding:0 18px;flex:1;opacity:.95}
.product .more{background:rgba(0,0,0,.15);padding:10px;font-size:11px;font-weight:600;letter-spacing:.5px}
.p-vie{background:var(--blue-box)}.p-salaire{background:var(--orange)}
.p-hypo{background:var(--green)}.p-mg{background:var(--pink)}

/* main */
.main{height:1270px;padding-top:20px}
.main .wrap{display:flex;gap:24px}
.content{width:630px}
.sidebar{width:346px}
.post{border:1px solid var(--line);padding:20px 24px 16px;margin-bottom:20px}
.post h2{color:var(--blue);font-size:30px;line-height:1.15;margin-bottom:14px}
.post p{margin-bottom:10px}
.arrows{list-style:none;margin:4px 0 12px}
.arrows li{padding-left:16px;position:relative;font-size:12.5px}
.arrows li::before{content:"";position:absolute;left:2px;top:7px;border:4px solid transparent;border-left:6px solid var(--red)}
.meta{font-size:11px;color:var(--muted);border-top:1px solid var(--line);padding-top:8px;margin-top:6px}
.meta b{color:var(--red);font-weight:600}
.feature{display:flex;gap:20px}
.feature-img{width:260px;height:200px;flex:none;background:linear-gradient(135deg,#cfe3ef,#8fb46a 70%,#5a7e3a)}
.feature h4{color:var(--red);font-size:18px;text-transform:none;margin-bottom:8px}
.btn-more{display:inline-block;border:1px solid #ccc;padding:6px 16px;font-size:11px;font-weight:700;color:#444;margin-top:10px}
.widget{border:1px solid var(--line);padding:20px 22px;margin-bottom:20px}
.widget h3{font-size:17px;color:#333;border-bottom:2px solid var(--red);padding-bottom:8px;margin-bottom:12px}
.widget p{font-size:12px;margin-bottom:6px}
.cities{list-style:none;margin-top:10px}
.cities li{display:flex;align-items:center;gap:8px;font-size:12px;padding:3px 0;border-bottom:1px dotted var(--line)}
.cities svg{width:10px;height:14px;flex:none}
.partner{height:260px;display:flex;align-items:center;justify-content:center}
.partner-badge{width:260px;height:140px;border:2px solid #222;background:#fff;display:flex;align-items:center;justify-content:center}
.partner-badge span{width:90px;height:90px;background:#222}

/* blog */
.blog{height:310px;background:var(--bg);padding-top:22px}
.blog h2{text-align:center;color:var(--blue);font-size:28px;margin-bottom:4px}
.blog .rule{width:60px;height:3px;background:var(--red);margin:0 auto 18px}
.cards{display:flex;gap:20px}
.card{flex:1;background:#fff;height:220px}
.card-img{height:110px}
.card .body{padding:8px 12px;font-size:11.5px;line-height:1.5}
.card .meta{border:0;padding:0;margin:0 0 4px}
.ci1{background:linear-gradient(135deg,#bcd9ec,#e9c9a8)}
.ci2{background:linear-gradient(135deg,#d8e7c6,#88b15c)}
.ci3{background:linear-gradient(135deg,#f1d6c2,#b9cfe0)}
.ci4{background:linear-gradient(135deg,#cfe0ee,#7ea85a)}

/* footer */
.site-footer{height:200px;background:var(--navy);color:#c4cbd9;font-size:11.5px;padding-top:24px}
.site-footer .wrap{display:flex;gap:30px}
.site-footer h4{color:#fff;font-size:14px;margin-bottom:10px}
.f-brand{width:200px;display:flex;flex-direction:column;align-items:center;gap:10px;padding-top:10px}
.f-brand .dot{width:90px;height:90px;border-radius:50%;background:var(--red)}
.f-brand .name{color:#fff;font-weight:700;font-size:15px}
.f-col{flex:1}
.f-col ul{list-style:none}
.f-col li{padding:1px 0}
.tweet{margin-bottom:8px}
.tweet a{color:#6fb8e8}
.contact-line{display:flex;gap:8px;align-items:flex-start;margin-bottom:6px}
.contact-line svg{width:12px;height:12px;margin-top:3px;flex:none}
.copyright{height:40px;background:var(--navy-dark);color:#8a94a8;font-size:11px;text-align:center;line-height:40px}
</style>
</head>
<body>

<header class="site-header">
  <div class="wrap">
    <div class="brand"><span class="brand-dot"></span><span class="brand-name">lepontdoriole.ca</span></div>
    <div class="topbar">
      <span><svg viewBox="0 0 24 24"><path fill="#d7262e" d="M6.6 10.8a15 15 0 0 0 6.6 6.6l2.2-2.2a1 1 0 0 1 1-.25 11.4 11.4 0 0 0 3.6.57 1 1 0 0 1 1 1V20a1 1 0 0 1-1 1A17 17 0 0 1 3 4a1 1 0 0 1 1-1h3.5a1 1 0 0 1 1 1c0 1.25.2 2.45.57 3.57a1 1 0 0 1-.25 1z"/></svg>1 800 555-0142</span>
      <span><svg viewBox="0 0 24 24"><path fill="#d7262e" d="M2 5h20v14H2zm2 2v.5l8 5 8-5V7l-8 5z"/></svg>contact@lepontdoriole.ca</span>
      <span>Français ▾</span>
    </div>
    <nav class="main-nav">
      <a class="active">Accueil</a><a>Produits</a><a>Soumission</a><a>Qui Sommes-Nous?</a><a>Nous Joindre</a>
    </nav>
  </div>
</header>

<section class="hero">
  <div class="hero-photo" role="img" aria-label="Famille souriante assise dans l'herbe sous un ciel clair"></div>
  <div class="hero-brand"><span class="sq"></span><span class="name">lepontdoriole.ca</span></div>
  <form class="quote-form">
    <h2>DEMANDE DE SOUMISSION</h2>
    <div class="qf-row"><label>Produit</label><div class="qf-select"></div></div>
    <div class="qf-row"><label>Type d'assurance</label><div class="qf-select"></div></div>
    <div class="qf-row qf-radios"><span><i></i>Demandeur</span><span><i></i>Co-Demandeur</span></div>
    <div class="qf-grid">
      <div class="qf-field">Prénom</div><div class="qf-field">Nom</div>
      <div class="qf-field">Téléphone</div><div class="qf-field">Courriel</div>
      <div class="qf-field">Date de naissance</div><div class="qf-field">Sexe</div>
      <div class="qf-field">Fumeur</div><div class="qf-field">Montant</div>
    </div>
    <div class="qf-foot"><div class="captcha">GM99</div><div class="qf-field">Code</div><span class="btn-send">ENVOI</span></div>
  </form>
</section>

<section class="products">
  <div class="wrap">
    <div class="product p-vie"><h3>Assurance vie</h3><p>Protégez ceux que vous aimez avec une couverture adaptée à votre budget et à vos besoins.</p><div class="more">SOUMISSIONNEZ</div></div>
    <div class="product p-salaire"><h3>Salaire</h3><p>Conservez votre revenu en cas d'invalidité grâce à une protection simple et abordable.</p><div class="more">SOUMISSIONNEZ</div></div>
    <div class="product p-hypo"><h3>Hypothécaire</h3><p>Assurez votre maison et la sécurité de votre famille au meilleur prix du marché.</p><div class="more">SOUMISSIONNEZ</div></div>
    <div class="product p-mg"><h3>Maladies graves</h3><p>Recevez un montant forfaitaire pour traverser une maladie grave en toute tranquillité.</p><div class="more">SOUMISSIONNEZ</div></div>
  </div>
</section>

<main class="main">
  <div class="wrap">
    <div class="content">
      <article class="post">
        <h2>Trouvez la meilleure assurance,<br>au meilleur prix!</h2>
        <p>Nous comparons pour vous les primes des principaux assureurs canadiens afin de vous offrir la protection qui convient le mieux à votre situation. Notre service est gratuit, rapide et sans engagement. Remplissez le formulaire et recevez une soumission personnalisée dans les plus brefs délais.</p>
        <p>Nos conseillers analysent votre profil, vos besoins et votre budget afin de vous présenter les meilleures options disponibles sur le marché.</p>
        <ul class="arrows">
          <li>Assurance vie permanente — Assurance vie temporaire</li>
          <li>Assurance invalidité — Assurance salaire</li>
          <li>Assurance prêt hypothécaire — Assurance prêt</li>
          <li>Assurance maladies graves</li>
          <li>Assurance frais funéraires</li>
        </ul>
        <p class="meta">Posted by <b>July 22, 2015</b> &nbsp;|&nbsp; <b>Comments</b></p>
      </article>

      <article class="post">
        <h2>Des conseillers en sécurité<br>financière compétents</h2>
        <p>Notre équipe est composée de conseillers certifiés qui vous accompagnent à chaque étape. Ils prennent le temps de répondre à vos questions et de vous expliquer clairement chacune des options offertes. Nous travaillons avec plusieurs compagnies reconnues afin de trouver la solution idéale pour vous et votre famille, partout au Québec.</p>
        <p class="meta">Posted by <b>July 22, 2015</b> &nbsp;|&nbsp; <b>Comments</b></p>
      </article>

      <article class="post">
        <h2>L'importance de ne pas payer trop cher</h2>
        <div class="feature">
          <div class="feature-img" role="img" aria-label="Couple souriant dans un parc"></div>
          <div>
            <h4>Comment procéder?</h4>
            <p>Il suffit de remplir notre formulaire en ligne. Un conseiller compare ensuite les offres de plusieurs assureurs et vous présente la meilleure prime pour votre profil, sans frais.</p>
            <p class="meta">July 22, 2015 &nbsp;|&nbsp; <b>Comments</b></p>
            <span class="btn-more">VIEW MORE</span>
          </div>
        </div>
      </article>
    </div>

    <aside class="sidebar">
      <div class="widget">
        <h3>Heures d'ouverture</h3>
        <p><b>Nos heures de service</b></p>
        <p>Lundi au vendredi : 9 h à 21 h</p>
        <p>Samedi : 10 h à 16 h</p>
        <p>Dimanche : fermé</p>
        <p>Sans frais : 1 800 555-0142</p>
      </div>
      <div class="widget">
        <h3>Nos bureaux</h3>
        <p><b>Siège social</b></p>
        <p>250, rue des Érables, Laval QC H7N 0A1</p>
        <ul class="cities">
          <li><svg viewBox="0 0 10 14"><path fill="#d7262e" d="M5 0a5 5 0 0 1 5 5c0 4-5 9-5 9S0 9 0 5a5 5 0 0 1 5-5z"/></svg>Montréal</li>
          <li><svg viewBox="0 0 10 14"><path fill="#d7262e" d="M5 0a5 5 0 0 1 5 5c0 4-5 9-5 9S0 9 0 5a5 5 0 0 1 5-5z"/></svg>Québec</li>
          <li><svg viewBox="0 0 10 14"><path fill="#d7262e" d="M5 0a5 5 0 0 1 5 5c0 4-5 9-5 9S0 9 0 5a5 5 0 0 1 5-5z"/></svg>Laval</li>
          <li><svg viewBox="0 0 10 14"><path fill="#d7262e" d="M5 0a5 5 0 0 1 5 5c0 4-5 9-5 9S0 9 0 5a5 5 0 0 1 5-5z"/></svg>Gatineau</li>
          <li><svg viewBox="0 0 10 14"><path fill="#d7262e" d="M5 0a5 5 0 0 1 5 5c0 4-5 9-5 9S0 9 0 5a5 5 0 0 1 5-5z"/></svg>Trois-Rivières</li>
          <li><svg viewBox="0 0 10 14"><path fill="#d7262e" d="M5 0a5 5 0 0 1 5 5c0 4-5 9-5 9S0 9 0 5a5 5 0 0 1 5-5z"/></svg>Sherbrooke</li>
          <li><svg viewBox="0 0 10 14"><path fill="#d7262e" d="M5 0a5 5 0 0 1 5 5c0 4-5 9-5 9S0 9 0 5a5 5 0 0 1 5-5z"/></svg>Longueuil</li>
          <li><svg viewBox="0 0 10 14"><path fill="#d7262e" d="M5 0a5 5 0 0 1 5 5c0 4-5 9-5 9S0 9 0 5a5 5 0 0 1 5-5z"/></svg>Saguenay</li>
          <li><svg viewBox="0 0 10 14"><path fill="#d7262e" d="M5 0a5 5 0 0 1 5 5c0 4-5 9-5 9S0 9 0 5a5 5 0 0 1 5-5z"/></svg>Rimouski</li>
        </ul>
      </div>
      <div class="partner"><div class="partner-badge"><span></span></div></div>
    </aside>
  </div>
</main>

<section class="blog">
  <div class="wrap">
    <h2>Recent Blog</h2>
    <div class="rule"></div>
    <div class="cards">
      <div class="card"><div class="card-img ci1" role="img" aria-label="Famille à la plage"></div><div class="body"><p class="meta">March 20, 2015 &nbsp;|&nbsp; 0 Comments</p><p>Comment choisir le bon montant d'assurance vie pour protéger votre famille.</p></div></div>
      <div class="card"><div class="card-img ci2" role="img" aria-label="Parents et enfant dans un champ"></div><div class="body"><p class="meta">March 20, 2015 &nbsp;|&nbsp; 0 Comments</p><p>Temporaire ou permanente : quelle assurance vie convient à votre situation?</p></div></div>
      <div class="card"><div class="card-img ci3" role="img" aria-label="Couple dans leur nouvelle maison"></div><div class="body"><p class="meta">March 20, 2015 &nbsp;|&nbsp; 0 Comments</p><p>Assurance hypothécaire : pourquoi comparer avant de signer chez votre banque.</p></div></div>
      <div class="card"><div class="card-img ci4" role="img" aria-label="Famille marchant dans un parc"></div><div class="body"><p class="meta">March 20, 2015 &nbsp;|&nbsp; 0 Comments</p><p>Cinq conseils pour réduire votre prime d'assurance maladies graves.</p></div></div>
    </div>
  </div>
</section>

<footer class="site-footer">
  <div class="wrap">
    <div class="f-brand"><span class="dot"></span><span class="name">lepontdoriole.ca</span></div>
    <div class="f-col">
      <h4>Type de protection</h4>
      <ul><li>Assurance vie</li><li>Assurance invalidité</li><li>Assurance hypothécaire</li><li>Assurance maladies graves</li><li>Assurance temporaire</li><li>Assurance permanente</li></ul>
    </div>
    <div class="f-col">
      <h4>Latest Tweets</h4>
      <p class="tweet">Nouvel article sur notre blogue : comment bien choisir votre protection. <a>#assurance</a></p>
      <p class="tweet">Obtenez votre soumission gratuite en moins de deux minutes. <a>lepontdoriole.ca</a></p>
    </div>
    <div class="f-col">
      <h4>Contact Us</h4>
      <div class="contact-line"><svg viewBox="0 0 10 14"><path fill="#d7262e" d="M5 0a5 5 0 0 1 5 5c0 4-5 9-5 9S0 9 0 5a5 5 0 0 1 5-5z"/></svg><span>250, rue des Érables<br>Laval QC H7N 0A1</span></div>
      <div class="contact-line"><svg viewBox="0 0 24 24"><circle cx="12" cy="12" r="10" fill="none" stroke="#d7262e" stroke-width="2.5"/><path d="M12 6v6l4 2" stroke="#d7262e" stroke-width="2.5" fill="none"/></svg><span>Lundi au vendredi 9 h à 21 h</span></div>
      <div class="contact-line"><svg viewBox="0 0 24 24"><path fill="#d7262e" d="M6.6 10.8a15 15 0 0 0 6.6 6.6l2.2-2.2a1 1 0 0 1 1-.25 11.4 11.4 0 0 0 3.6.57 1 1 0 0 1 1 1V20a1 1 0 0 1-1 1A17 17 0 0 1 3 4a1 1 0 0 1 1-1h3.5a1 1 0 0 1 1 1c0 1.25.2 2.45.57 3.57a1 1 0 0 1-.25 1z"/></svg><span>Sans frais : 1 800 555-0142</span></div>
      <div class="contact-line"><svg viewBox="0 0 24 24"><path fill="#d7262e" d="M2 5h20v14H2zm2 2v.5l8 5 8-5V7l-8 5z"/></svg><span>contact@lepontdoriole.ca</span></div>
    </div>
  </div>
</footer>
<div class="copyright">Copyright © 2015, lepontdoriole.ca. Tous droits réservés.</div>

</body>
</html>
```